Business Cards Needed for Innovative Healthcare Marketing Company

We are a marketing company focused on healthcare. Our company is all about rebranding yourself renewing your image and generating results. The phoenix stands for "reborn" or "rising" which we provide new brands for our clients we take their old brands and renew it with creativity and innovation. I am looking for a business card with color dimension. I have attached an example of a card I think has the look and feel of what I am trying to accomplish. I like that the card example has black and grey font colors, I like the font placement and the small logo, I really like the use of the colors on the right those are the colors of my logo. My logo is phoenix so maybe incorporating flames similar to that design. I would like the back a solid color maybe red with an opaque version of the logo and website. As a marketing company I am always open to creative liberty!

Target Market(s)

Doctors and business professionals.

Industry/Entity Type

Marketing

Contact Information for Business Card

Valcorne Health Care Marketing
Marla Tenwick- CEO
#(512)638-2974
email-marla@valcorne.com
website- valcorne.com

Font styles to use
Sans Serif

Colors
ec1f27
f37122
ffc214
fbed22
fbf289
f04a50

Requirements
Must have
• The logo and required information
Nice to have
• icons by the information
Should not have
• child like font

```html
<!DOCTYPE html>
<html lang="en">
<head>
<meta charset="utf-8">
<title>Valcorne Health Care Marketing – Business Card</title>
<link rel="stylesheet" href="https://fonts.googleapis.com/css2?family=Lato:wght@300;400;700&display=swap">
<style>
  :root {
    --red: #ec1f27;
    --deep-red: #c8232b;
    --orange: #f37122;
    --amber: #f39a2a;
    --yellow: #ffc214;
    --lemon: #fbed22;
    --paper: #ffffff;
    --paper-shade: #f1f1f1;
    --ink: #3a3a3a;
    --stage: #e6e4e1;
  }
  * { box-sizing: border-box; margin: 0; padding: 0; }
  html, body { width: 1200px; height: 1023px; overflow: hidden; }
  body {
    background: var(--stage);
    font-family: "Lato", sans-serif;
    position: relative;
  }
  .card {
    position: absolute;
    width: 735px;
    height: 420px;
    border-radius: 22px;
    overflow: hidden;
    box-shadow: 0 6px 18px rgba(0,0,0,0.18);
  }
  /* ---------- front ---------- */
  .card-front {
    left: 60px; top: 55px;
    background: linear-gradient(160deg, var(--paper) 0%, var(--paper-shade) 100%);
  }
  .card-front .edge-bands { position: absolute; left: 0; bottom: 0; width: 735px; height: 130px; }
  .brand-lockup { position: absolute; left: 48px; top: 92px; }
  .brand-row { display: flex; align-items: center; gap: 16px; }
  .brand-dot { width: 46px; height: 46px; border-radius: 50%; background: var(--orange); flex: none; }
  .brand-name {
    font-weight: 300; font-size: 66px; letter-spacing: 3px;
    color: var(--deep-red); line-height: 1;
  }
  .brand-rule { height: 1px; background: var(--deep-red); margin: 10px 0 8px 62px; width: 270px; }
  .brand-tagline {
    margin-left: 62px; font-weight: 300; font-size: 20px; letter-spacing: 1px;
    color: var(--deep-red); line-height: 1.2;
  }
  .name-tab { position: absolute; right: 36px; top: 0; width: 30px; height: 30px; background: var(--red); }
  .person { position: absolute; right: 80px; top: 40px; text-align: right; }
  .person-name { font-weight: 700; font-size: 32px; color: var(--red); letter-spacing: 0.5px; line-height: 1.2; }
  .person-title { font-size: 15px; color: var(--orange); margin-top: 2px; }
  .divider { position: absolute; left: 48px; right: 48px; top: 246px; height: 1px; background: var(--amber); }
  .contact-list { position: absolute; left: 48px; top: 260px; list-style: none; }
  .contact-item { display: flex; align-items: center; gap: 10px; font-size: 17px; color: var(--ink); height: 28px; }
  .contact-icon { width: 20px; height: 20px; flex: none; }
  /* ---------- back ---------- */
  .card-back {
    left: 405px; top: 548px;
    background: radial-gradient(ellipse at 60% 55%, var(--amber) 0%, var(--orange) 75%);
  }
  .card-back .edge-bands { position: absolute; left: 0; top: 0; width: 140px; height: 420px; }
  .back-lockup {
    position: absolute; left: 170px; right: 40px; top: 95px;
    display: flex; flex-direction: column; align-items: center; color: var(--paper);
  }
  .back-dot { width: 80px; height: 80px; border-radius: 50%; background: rgba(255,255,255,0.85); margin-bottom: 18px; }
  .back-name { font-weight: 300; font-size: 64px; letter-spacing: 4px; line-height: 1; }
  .back-rule { width: 300px; height: 1px; background: var(--deep-red); margin: 10px 0 8px; }
  .back-tagline { font-weight: 700; font-size: 19px; letter-spacing: 1px; }
  .back-web { font-size: 16px; letter-spacing: 2px; margin-top: 40px; }
</style>
</head>
<body>

<section class="card card-front" aria-label="Business card front">
  <svg class="edge-bands" viewBox="0 0 735 130" aria-hidden="true">
    <polygon points="0,108 430,108 430,130 0,130" fill="var(--orange)"/>
    <polygon points="430,100 480,40 735,40 735,130 430,130" fill="var(--yellow)"/>
    <polygon points="440,108 470,70 735,70 735,130 430,130" fill="var(--lemon)" opacity="0.45"/>
  </svg>

  <div class="name-tab"></div>
  <div class="person">
    <p class="person-name">Marla Tenwick</p>
    <p class="person-title">Title</p>
  </div>

  <div class="brand-lockup">
    <div class="brand-row">
      <span class="brand-dot"></span>
      <span class="brand-name">VALCORNE</span>
    </div>
    <div class="brand-rule"></div>
    <p class="brand-tagline">HEALTHCARE MARKETING</p>
  </div>

  <div class="divider"></div>

  <ul class="contact-list">
    <li class="contact-item">
      <svg class="contact-icon" viewBox="0 0 20 20" aria-hidden="true">
        <rect width="20" height="20" rx="4" fill="var(--red)"/>
        <path d="M6 5 l2 0 1 3 -1.5 1 a7 7 0 0 0 3.5 3.5 l1 -1.5 3 1 0 2 a1.5 1.5 0 0 1 -1.5 1.5 A9 9 0 0 1 4.5 6.5 1.5 1.5 0 0 1 6 5z" fill="#fff"/>
      </svg>
      (512)638-2974
    </li>
    <li class="contact-item">
      <svg class="contact-icon" viewBox="0 0 20 20" aria-hidden="true">
        <rect width="20" height="20" rx="4" fill="var(--red)"/>
        <rect x="4" y="6" width="12" height="8" fill="none" stroke="#fff" stroke-width="1.5"/>
        <path d="M4 6 l6 5 6 -5" fill="none" stroke="#fff" stroke-width="1.5"/>
      </svg>
      marla@valcorne.com
    </li>
    <li class="contact-item">
      <svg class="contact-icon" viewBox="0 0 20 20" aria-hidden="true">
        <circle cx="10" cy="10" r="8.5" fill="none" stroke="var(--red)" stroke-width="1.5"/>
        <ellipse cx="10" cy="10" rx="3.5" ry="8.5" fill="none" stroke="var(--red)" stroke-width="1.2"/>
        <path d="M2 10 h16 M3.5 6 h13 M3.5 14 h13" stroke="var(--red)" stroke-width="1.2"/>
      </svg>
      www.valcorne.com
    </li>
  </ul>
</section>

<section class="card card-back" aria-label="Business card back">
  <svg class="edge-bands" viewBox="0 0 140 420" aria-hidden="true">
    <polygon points="0,0 22,0 22,420 0,420" fill="var(--paper)"/>
    <polygon points="22,0 120,0 120,200 22,230" fill="var(--yellow)"/>
  </svg>

  <div class="back-lockup">
    <span class="back-dot"></span>
    <p class="back-name">VALCORNE</p>
    <div class="back-rule"></div>
    <p class="back-tagline">HEALTHCARE MARKETING</p>
    <p class="back-web">www.valcorne.com</p>
  </div>
</section>

</body>
</html>
```